Marlow Sail Works President Business Card Carbon fiber catamarans

Hi.. I need a new business card design.. I am the President of a high tech yacht builder. We build Carbon Fiber go fast catamarans... Maybe we use the file I am sharing to you as the back of the card.. We need to look cool and crisp ...

Target Market(s)

Affluent People who will purchase a cool yacht

Industry/Entity Type

Custom Yacht Builder

Contact Information for Business Card

Dean Pellway , President, 731.508.2164 USA

Font styles to use
Serif

Requirements
Must have
• the clean crisp cool feel
Nice to have
• clean and crisp
Should not have
• Bold ugly

```html
<!DOCTYPE html>
<html lang="en">
<head>
<meta charset="utf-8">
<title>Marlow Sail Works – Business Card</title>
<link href="https://fonts.googleapis.com/css2?family=Roboto:wght@400;500&display=swap" rel="stylesheet">
<style>
  :root {
    --bg: #dcdcdc;
    --card-white: #ffffff;
    --card-dark: #151515;
    --ink: #1c1c1c;
    --ink-soft: #555555;
    --rule: #c8c8c8;
    --logo-grey: #5a5a5a;
    --logo-silver: #c4c4c4;
  }
  * { margin: 0; padding: 0; box-sizing: border-box; }
  html, body { width: 1200px; height: 1200px; overflow: hidden; }
  body {
    background: var(--bg);
    font-family: "Roboto", Arial, sans-serif;
    position: relative;
  }
  .card {
    position: absolute;
    left: 262px;
    width: 686px;
    height: 392px;
    border-radius: 18px;
    overflow: hidden;
  }
  .card-front { top: 165px; background: var(--card-white); }
  .card-back  { top: 653px; background: var(--card-dark); }

  .brand {
    position: absolute;
    display: flex;
    align-items: center;
    gap: 10px;
    white-space: nowrap;
  }
  .brand-mark { display: block; flex: none; }
  .brand-name { font-weight: 400; letter-spacing: 0.1em; text-transform: uppercase; line-height: 1; }

  .card-front .brand { left: 60px; top: 208px; transform: translateY(-50%); max-width: 270px; }
  .card-front .brand-mark { width: 20px; height: 20px; background: var(--logo-grey); }
  .card-front .brand-name { font-size: 17px; color: var(--logo-grey); }

  .divider {
    position: absolute;
    left: 346px; top: 90px;
    width: 1px; height: 240px;
    background: var(--rule);
  }
  .contact { position: absolute; left: 369px; top: 101px; color: var(--ink-soft); }
  .person-name { font-size: 21px; font-weight: 500; color: var(--ink); letter-spacing: 0.03em; line-height: 1.2; }
  .person-title { font-size: 15px; font-weight: 500; margin-top: 2px; }
  .address { font-size: 15px; line-height: 19px; margin-top: 16px; }
  .lines { list-style: none; margin-top: 16px; font-size: 15px; line-height: 19.5px; }
  .lines li { display: flex; align-items: center; gap: 9px; }
  .lines svg { width: 13px; height: 13px; fill: var(--ink); flex: none; }

  .texture {
    position: absolute; inset: 0;
    background: radial-gradient(ellipse at 50% 45%, #2a2a2a 0%, #141414 70%, #0c0c0c 100%);
  }
  .card-back .brand { left: 50%; top: 50%; transform: translate(-50%, -50%); gap: 14px; }
  .card-back .brand-mark { width: 28px; height: 28px; background: var(--logo-silver); }
  .card-back .brand-name { font-size: 28px; color: var(--logo-silver); }
</style>
</head>
<body>
  <section class="card card-front" aria-label="Card front">
    <div class="brand">
      <span class="brand-mark"></span>
      <span class="brand-name">Marlow Sail Works</span>
    </div>
    <div class="divider"></div>
    <div class="contact">
      <p class="person-name">DEAN PELLWAY</p>
      <p class="person-title">President</p>
      <p class="address">214 Harbor Crest Road<br>Newport, Rhode Island 02840</p>
      <ul class="lines">
        <li><svg viewBox="0 0 16 16"><path d="M3.5 1l3 3-1.6 2a9 9 0 0 0 5.1 5.1l2-1.6 3 3-2 2.5C6.5 15 1 9.5 1 3z"/></svg>731-508-2164</li>
        <li><svg viewBox="0 0 16 16"><path d="M4 0h8a1 1 0 0 1 1 1v14a1 1 0 0 1-1 1H4a1 1 0 0 1-1-1V1a1 1 0 0 1 1-1zm1 2v10h6V2zm3 11a1 1 0 1 0 0 2 1 1 0 0 0 0-2z"/></svg>731-508-7390</li>
        <li><svg viewBox="0 0 16 16"><path d="M4 1h8v4H4zM1 6h14v6h-2v3H3v-3H1zm4 5v3h6v-3z"/></svg>731-508-4415</li>
        <li><svg viewBox="0 0 16 16"><path d="M1 3h14v2L8 9 1 5zm0 4l7 4 7-4v6H1z"/></svg>name@marlowsail.com</li>
        <li><svg viewBox="0 0 16 16"><circle cx="8" cy="8" r="7"/><path d="M1 8h14M8 1c-3 3-3 11 0 14M8 1c3 3 3 11 0 14" stroke="#fff" stroke-width="1.2" fill="none"/></svg>www.marlowsail.com</li>
      </ul>
    </div>
  </section>

  <section class="card card-back" aria-label="Card back">
    <div class="texture" role="img" aria-label="Dark perforated carbon-metal texture"></div>
    <div class="brand">
      <span class="brand-mark"></span>
      <span class="brand-name">Marlow Sail Works</span>
    </div>
  </section>
</body>
</html>
```